Car wash line needed for the pylon inscription

We need a design template / print template for our advertising pylon so that the Korvane plates can be printed. The area to be printed is approx. 1.5m wide and approx. 2.70m high. We operate a car wash about 30m long. The washing rollers are equipped with scratch-free Velmo Tex foam material. Before the vehicle is put into the car wash it gets a manual high pressure pre-wash. There are four different washing programs: basic laundry € 7.50 (wheel cleaning, intensive washing, gloss drying comfort care € 10.50 (like base + active foam) special care € 13.00 (like comfort + glossy sealing with lotus wax) premium care € 15.50 (like special care + Underbody wash) The pylon is right on the driveway on a busy road, we want to achieve maximum attention with the pylons. It should not be too much content because the vehicles drive past it, due to an immediate gyro, the speed is however at about 40Km / h. Opening hours Mon-Fri. 08: 00-19: 00 Sat 07: 00-19: 00 The Korvane plates are red. The enclosed files show our pylon with a little appealing design proposal our advertising agency and the real local places. For the opinion you can see on the following link a youtube video with a comparable car wash like ours, the washing process is well illustrated there. https://www.clipvault-demo.net/watch?v=Qk7rTzP2mLw Furthermore, we have a bonus card system who has washed our car 10 times gets the 11 laundry for free. From foam additives we use active foam from the comfort care and from the special care gets the vehicle lotus wax, which has the effect that the paint is sealed and keeps the shine longer. We need a design template / print template for our advertising pylon so that the Korvane plates can be printed. The area to be printed is approx. 1.5m wide and approx. 2.70m high. We operate a car wash about 30m long. The washing rollers are equipped with scratch-free Velmo Tex foam material. Before the vehicle is put into the car wash it gets a manual high pressure pre-wash. There are four different washing programs: basic laundry € 7.50 (wheel cleaning, intensive washing, gloss drying comfort care € 10.50 (like base + active foam) special care € 13.00 (like comfort + glossy sealing with lotus wax) premium care € 15.50 (like special care + Underbody wash) The pylon is right on the driveway on a busy road, we want to achieve maximum attention with the pylons. It should not be too much content because the vehicles drive past it, due to an immediate gyro, the speed is however at about 40Km / h. Opening hours Mon-Fri. 08: 00-19: 00 Sat 07: 00-19: 00 The Korvane plates are red. The enclosed files show our pylon with a little appealing design proposal our advertising agency and the real local places. For the opinion you can see on the following link a youtube video with a comparable car wash like ours, the washing process is well illustrated there. https://www.clipvault-demo.net/watch?v=Qk7rTzP2mLw Furthermore, we have a bonus card system who has washed our car 10 times gets the 11 laundry for free. From foam additives we use active foam from the comfort care and from the special care gets the vehicle lotus wax, which has the effect that the paint is sealed and keeps the shine longer. We need a design template / print template for our advertising pylon so that the Korvane plates can be printed. The area to be printed is approx. 1.5m wide and approx. 2.70m high. We operate a car wash about 30m long. The washing rollers are equipped with scratch-free Velmo Tex foam material. Before the vehicle is put into the car wash it gets a manual high pressure pre-wash. There are four different washing programs: basic laundry € 7.50 (wheel cleaning, intensive washing, gloss drying comfort care € 10.50 (like base + active foam) special care € 13.00 (like comfort + glossy sealing with lotus wax) premium care € 15.50 (like special care + Underbody wash) The pylon is right on the driveway on a busy road, we want to achieve maximum attention with the pylons. It should not be too much content because the vehicles drive past it, due to an immediate gyro, the speed is however at about 40Km / h. Opening hours Mon-Fri. 08: 00-19: 00 Sat 07: 00-19: 00 The Korvane plates are red. The enclosed files show our pylon with a little appealing design proposal our advertising agency and the real local places. For the opinion you can see on the following link a youtube video with a comparable car wash like ours, the washing process is well illustrated there. https://www.clipvault-demo.net/watch?v=Qk7rTzP2mLw Furthermore, we have a bonus card system who has washed our car 10 times gets the 11 laundry for free. From foam additives we use active foam from the comfort care and from the special care gets the vehicle lotus wax, which has the effect that the paint is sealed and keeps the shine longer. We need a design template / print template for our advertising pylon so that the Korvane plates can be printed. The area to be printed is approx. 1.5m wide and approx. 2.70m high. We operate a car wash about 30m long. The washing rollers are equipped with scratch-free Velmo Tex foam material. Before the vehicle is put into the car wash it gets a manual high pressure pre-wash. There are four different washing programs: basic laundry € 7.50 (wheel cleaning, intensive washing, gloss drying comfort care € 10.50 (like base + active foam) special care € 13.00 (like comfort + glossy sealing with lotus wax) premium care € 15.50 (like special care + Underbody wash) The pylon is right on the driveway on a busy road, we want to achieve maximum attention with the pylons. It should not be too much content because the vehicles drive past it, due to an immediate gyro, the speed is however at about 40Km / h. Opening hours Mon-Fri. 08: 00-19: 00 Sat 07: 00-19: 00 The Korvane plates are red. The enclosed files show our pylon with a little appealing design proposal our advertising agency and the real local places. For the opinion you can see on the following link a youtube video with a comparable car wash like ours, the washing process is well illustrated there. https://www.clipvault-demo.net/watch?v=Qk7rTzP2mLw Furthermore, we have a bonus card system who has washed our car 10 times gets the 11 laundry for free. From foam additives we use active foam from the comfort care and from the special care gets the vehicle lotus wax, which has the effect that the paint is sealed and keeps the shine longer. We need a design template / print template for our advertising pylon so that the Korvane plates can be printed. The area to be printed is approx. 1.5m wide and approx. 2.70m high. We operate a car wash about 30m long. The washing rollers are equipped with scratch-free Velmo Tex foam material. Before the vehicle is put into the car wash it gets a manual high pressure pre-wash. There are four different washing programs: basic laundry € 7.50 (wheel cleaning, intensive washing, gloss drying comfort care € 10.50 (like base + active foam) special care € 13.00 (like comfort + glossy sealing with lotus wax) premium care € 15.50 (like special care + Underbody wash) The pylon is right on the driveway on a busy road, we want to achieve maximum attention with the pylons. It should not be too much content because the vehicles drive past it, due to an immediate gyro, the speed is however at about 40Km / h. Opening hours Mon-Fri. 08: 00-19: 00 Sat 07: 00-19: 00 The Korvane plates are red. The enclosed files show our pylon with a little appealing design proposal our advertising agency and the real local places. For the opinion you can see on the following link a youtube video with a comparable car wash like ours, the washing process is well illustrated there. https://www.clipvault-demo.net/watch?v=Qk7rTzP2mLw Furthermore, we have a bonus card system who has washed our car 10 times gets the 11 laundry for free. From foam additives we use active foam from the comfort care and from the special care gets the vehicle lotus wax, which has the effect that the paint is sealed and keeps the shine longer. We need a design template / print template for our advertising pylon so that the Korvane plates can be printed. The area to be printed is approx. 1.5m wide and approx. 2.70m high. We operate a car wash about 30m long. The washing rollers are equipped with scratch-free Velmo Tex foam material. Before the vehicle is put into the car wash it gets a manual high pressure pre-wash. There are four different washing programs: basic laundry € 7.50 (wheel cleaning, intensive washing, gloss drying comfort care € 10.50 (like base + active foam) special care € 13.00 (like comfort + glossy sealing with lotus wax) premium care € 15.50 (like special care + Underbody wash) The pylon is right on the driveway on a busy road, we want to achieve maximum attention with the pylons. It should not be too much content because the vehicles drive past it, due to an immediate gyro, the speed is however at about 40Km / h. Opening hours Mon-Fri. 08: 00-19: 00 Sat 07: 00-19: 00 The Korvane plates are red. The enclosed files show our pylon with a little appealing design proposal our advertising agency and the real local places. For the opinion you can see on the following link a youtube video with a comparable car wash like ours, the washing process is well illustrated there. https://www.clipvault-demo.net/watch?v=Qk7rTzP2mLw Furthermore, we have a bonus card system who has washed our car 10 times gets the 11 laundry for free. From foam additives we use active foam from the comfort care and from the special care gets the vehicle lotus wax, which has the effect that the paint is sealed and keeps the shine longer. We need a design template / print template for our advertising pylon so that the Korvane plates can be printed. The area to be printed is approx. 1.5m wide and approx. 2.70m high. We operate a car wash about 30m long. The washing rollers are equipped with scratch-free Velmo Tex foam material. Before the vehicle is put into the car wash it gets a manual high pressure pre-wash. There are four different washing programs: basic laundry € 7.50 (wheel cleaning, intensive washing, gloss drying comfort care € 10.50 (like base + active foam) special care € 13.00 (like comfort + glossy sealing with lotus wax) premium care € 15.50 (like special care + Underbody wash) The pylon is right on the driveway on a busy road, we want to achieve maximum attention with the pylons. It should not be too much content because the vehicles drive past it, due to an immediate gyro, the speed is however at about 40Km / h. Opening hours Mon-Fri. 08: 00-19: 00 Sat 07: 00-19: 00 The Korvane plates are red. The enclosed files show our pylon with a little appealing design proposal our advertising agency and the real local places. For the opinion you can see on the following link a youtube video with a comparable car wash like ours, the washing process is well illustrated there. https://www.clipvault-demo.net/watch?v=Qk7rTzP2mLw Furthermore, we have a bonus card system who has washed our car 10 times gets the 11 laundry for free. From foam additives we use active foam from the comfort care and from the special care gets the vehicle lotus wax, which has the effect that the paint is sealed and keeps the shine longer. We need a design template / print template for our advertising pylon so that the Korvane plates can be printed. The area to be printed is approx. 1.5m wide and approx. 2.70m high. We operate a car wash about 30m long. The washing rollers are equipped with scratch-free Velmo Tex foam material. Before the vehicle is put into the car wash it gets a manual high pressure pre-wash. There are four different washing programs: basic laundry € 7.50 (wheel cleaning, intensive washing, gloss drying comfort care € 10.50 (like base + active foam) special care € 13.00 (like comfort + glossy sealing with lotus wax) premium care € 15.50 (like special care + Underbody wash) The pylon is right on the driveway on a busy road, we want to achieve maximum attention with the pylons. It should not be too much content because the vehicles drive past it, due to an immediate gyro, the speed is however at about 40Km / h. Opening hours Mon-Fri. 08: 00-19: 00 Sat 07: 00-19: 00 The Korvane plates are red. The enclosed files show our pylon with a little appealing design proposal our advertising agency and the real local places. For the opinion you can see on the following link a youtube video with a comparable car wash like ours, the washing process is well illustrated there. https://www.clipvault-demo.net/watch?v=Qk7rTzP2mLw Furthermore, we have a bonus card system who has washed our car 10 times gets the 11 laundry for free. From foam additives we use active foam from the comfort care and from the special care gets the vehicle lotus wax, which has the effect that the paint is sealed and keeps the shine longer. We need a design template / print template for our advertising pylon so that the Korvane plates can be printed. The area to be printed is approx. 1.5m wide and approx. 2.70m high. We operate a car wash about 30m long. The washing rollers are equipped with scratch-free Velmo Tex foam material. Before the vehicle is put into the car wash it gets a manual high pressure pre-wash. There are four different washing programs: basic laundry € 7.50 (wheel cleaning, intensive washing, gloss drying comfort care € 10.50 (like base + active foam) special care € 13.00 (like comfort + glossy sealing with lotus wax) premium care € 15.50 (like special care + Underbody wash) The pylon is right on the driveway on a busy road, we want to achieve maximum attention with the pylons. It should not be too much content because the vehicles drive past it, due to an immediate gyro, the speed is however at about 40Km / h. Opening hours Mon-Fri. 08: 00-19: 00 Sat 07: 00-19: 00 The Korvane plates are red. The enclosed files show our pylon with a little appealing design proposal our advertising agency and the real local places. For the opinion you can see on the following link a youtube video with a comparable car wash like ours, the washing process is well illustrated there. https://www.clipvault-demo.net/watch?v=Qk7rTzP2mLw Furthermore, we have a bonus card system who has washed our car 10 times gets the 11 laundry for free. From foam additives we use active foam from the comfort care and from the special care gets the vehicle lotus wax, which has the effect that the paint is sealed and keeps the shine longer.

Target Market(s)

germany

Colors

Designer to choose colors to be used in the design.

Requirements
Must have
• Print template for the print job in the accepted formats. Of course, the design must be in German
Nice to have
• Colors that attract attention, but are still serious. The content must be perceived when passing by and the customers must be aware of the car wash.
Should not have
• Kitschiges Design Too much content which takes longer to be read.

```html
<!DOCTYPE html>
<html lang="de">
<head>
<meta charset="utf-8">
<title>Autowäsche – Pylon</title>
<link rel="stylesheet" href="https://fonts.googleapis.com/css2?family=Anton&family=Roboto:ital,wght@0,400;0,700;1,700;1,900&family=Roboto+Condensed:ital,wght@1,800&display=swap">
<style>
  :root {
    --bg: #e6e6e4;
    --paper: #ffffff;
    --yellow: #f7c600;
    --navy: #0b1f3f;
    --panel-top: #0e3d86;
    --panel-bottom: #082864;
    --footer: #0b1a4d;
    --stripe: #1ea4e6;
    --red: #e3161b;
    --white: #ffffff;
    --sky-1: #bfe8fb;
    --sky-2: #1b8fd9;
  }
  * { box-sizing: border-box; margin: 0; padding: 0; }
  html, body { width: 1200px; height: 1148px; overflow: hidden; background: var(--bg); }
  .poster {
    position: absolute; left: 320px; top: 20px;
    width: 560px; height: 1108px;
    background: var(--paper);
    font-family: "Roboto", Arial, sans-serif;
  }
  .frame {
    position: absolute; inset: 8px;
    border: 16px solid var(--yellow);
    border-radius: 44px;
  }
  .brand {
    position: absolute; left: 42px; top: 40px;
    display: flex; align-items: center; gap: 6px;
  }
  .brand-dot { width: 16px; height: 16px; border-radius: 50%; background: var(--red); }
  .brand-name { font-size: 11px; font-weight: 700; color: var(--navy); text-transform: uppercase; }
  .hero-art {
    position: absolute; left: 60px; top: 66px; width: 440px; height: 180px;
    border-radius: 90px 90px 20px 20px;
    background: linear-gradient(160deg, var(--sky-1), var(--sky-2));
  }
  .title {
    position: absolute; left: 0; right: 0; top: 258px; height: 118px;
    background: var(--paper);
    font-family: "Anton", Impact, sans-serif;
    font-size: 112px; line-height: 118px; text-align: center;
    color: var(--navy); letter-spacing: -1px;
  }
  .benefits {
    position: absolute; left: 40px; right: 40px; top: 384px; height: 462px;
    background: linear-gradient(180deg, var(--panel-top), var(--panel-bottom));
    padding: 28px 22px 0 22px;
    list-style: none;
  }
  .benefit {
    display: flex; gap: 14px; align-items: flex-start;
    margin-bottom: 30px;
    color: var(--white); font-style: italic; font-weight: 700;
    font-size: 22px; line-height: 27px;
  }
  .tick { flex: 0 0 40px; width: 40px; height: 40px; margin-top: 2px; }
  .stripe {
    position: absolute; left: 40px; right: 40px; top: 846px; height: 8px;
    background: var(--stripe);
  }
  .offer {
    position: absolute; left: 40px; right: 40px; top: 854px; height: 214px;
    background: var(--footer);
    border-radius: 0 0 18px 18px;
  }
  .offer-tag {
    position: absolute; right: 14px; top: 14px;
    background: var(--red); color: var(--white);
    font-style: italic; font-weight: 900; font-size: 21px; line-height: 23px;
    padding: 6px 14px 6px 22px;
    clip-path: polygon(10px 0, 100% 0, 100% 100%, 0 100%);
  }
  .car-art {
    position: absolute; left: 22px; top: 78px; width: 150px; height: 56px;
    border-radius: 28px 40px 8px 8px;
    background: linear-gradient(180deg, #2b3f7a, #15275c);
  }
  .offer-kicker {
    position: absolute; right: 18px; top: 90px;
    color: var(--yellow); font-weight: 700; font-size: 24px;
  }
  .offer-headline {
    position: absolute; left: 0; right: 0; top: 118px; text-align: center;
    font-family: "Roboto Condensed", Arial, sans-serif;
    font-style: italic; font-weight: 800; font-size: 38px;
    color: var(--white);
  }
  .hours {
    position: absolute; left: 0; right: 0; top: 166px; text-align: center;
    color: var(--white); line-height: 19px;
  }
  .hours-label { font-size: 12px; text-transform: uppercase; }
  .hours-times { font-size: 17px; font-weight: 700; }
</style>
</head>
<body>
  <main class="poster">
    <div class="frame"></div>
    <div class="brand">
      <span class="brand-dot"></span>
      <span class="brand-name">Waschpark Sonnhof</span>
    </div>
    <div class="hero-art" role="img" aria-label="Illustration: glänzendes blaues Auto in einer Wasserwelle"></div>
    <h1 class="title">AUTOWÄSCHE</h1>

    <ul class="benefits">
      <li class="benefit">
        <svg class="tick" viewBox="0 0 40 40" aria-hidden="true"><circle cx="18" cy="22" r="17" fill="#e3161b"/><path d="M9 22l7 7 20-22" fill="none" stroke="#fff" stroke-width="5" stroke-linecap="round" stroke-linejoin="round"/></svg>
        <span>Unsere verschiedenen Waschprogramme garantieren Ihnen echte Qualität und</span>
      </li>
      <li class="benefit">
        <svg class="tick" viewBox="0 0 40 40" aria-hidden="true"><circle cx="18" cy="22" r="17" fill="#e3161b"/><path d="M9 22l7 7 20-22" fill="none" stroke="#fff" stroke-width="5" stroke-linecap="round" stroke-linejoin="round"/></svg>
        <span>Alle unsere Waschprogramme nutzen Aktiv-Schaum</span>
      </li>
      <li class="benefit">
        <svg class="tick" viewBox="0 0 40 40" aria-hidden="true"><circle cx="18" cy="22" r="17" fill="#e3161b"/><path d="M9 22l7 7 20-22" fill="none" stroke="#fff" stroke-width="5" stroke-linecap="round" stroke-linejoin="round"/></svg>
        <span>Neuwertiger Waschtechnik zu glänzenden Ergebnissen</span>
      </li>
      <li class="benefit">
        <svg class="tick" viewBox="0 0 40 40" aria-hidden="true"><circle cx="18" cy="22" r="17" fill="#e3161b"/><path d="M9 22l7 7 20-22" fill="none" stroke="#fff" stroke-width="5" stroke-linecap="round" stroke-linejoin="round"/></svg>
        <span>Und nutzen Sie unsere Bonuskarte. Nach 10 Wäschen erhalten 1 Wäsche kostenlos nach Wahl</span>
      </li>
    </ul>

    <div class="stripe"></div>
    <section class="offer">
      <p class="offer-tag">Perfekte Wäsche<br>auch für Ihr Auto</p>
      <div class="car-art" role="img" aria-label="Linienzeichnung eines Sportwagens mit Glanzsternen"></div>
      <p class="offer-kicker">ETWAS BESONDERES</p>
      <p class="offer-headline">ZUSÄTZLICH LOTUSWACHS</p>
      <div class="hours">
        <p class="hours-label">Öffnungszeiten</p>
        <p class="hours-times">Mo-Frei. 08:00-19:00 Uhr, Sa 07:00-19:00 Uhr</p>
      </div>
    </section>
  </main>
</body>
</html>
```